Byte Wardens Inc. IT Services and Sales

We need a new business card design for our new company. We have a current logo but are open and encourage any redesigns.

Byte Wardens is derived in our history from computer gaming. (NovaSiege References, STORM UNBROKEN!!!). We as a group have been together since high school (2002). Our friendships brought us together and now we are all business partners providing IT Support and Consultation Services ranging from fixing small issues like printers, home networking, pc building to custom application development and managed cloud and it networks for our clients.
We would like our design to communicate that we strive to be the best (we are born gamers and have a highly competitive instinct) and offer solutions to problems that other companies just simply say we can't do it. We are always looking to go above and beyond for our clients, learning our clients business and figuring out ways to help them make more money by optimizing the way they do business, offering solutions so they can grow their business and helping everyone utilize the technology they have or advise them with the technology they need to succeed.

Attached are things we have on our computers and logo's we have used.
One is a desktop background
while the other should be our logo.

Again, we are open to and encourage any logo redesigns in hope things can help with the direction we are looking into.

Please add a place for email as our current cards have no email and it makes us very sad.
Updates

Hi All,

Just wanted to say thank you for all those who submitted a design. We've updated our project to include the fact that we are open and encourage a logo redesign. Also, this project is now committed to payment.

Target Market(s)

We will be handing these out to all our future business prospects. Prospects are usually business owners that can be in any industry. They look to us to be cutting edge or professional.

Industry/Entity Type

High School

Requirements
Must have
• name, title, work, fax, and cell phone, address and email

```html
<!DOCTYPE html>
<html lang="en">
<head>
<meta charset="utf-8">
<title>Byte Wardens Inc. – Business Card</title>
<link rel="stylesheet" href="https://fonts.googleapis.com/css2?family=Open+Sans:ital,wght@0,300;0,400;0,700;1,400;1,700&display=swap">
<style>
  :root {
    --backdrop: #3a3a3a;
    --card: #0a0a0a;
    --card-glow: #2a2a2a;
    --band: #ffffff;
    --stripe-grey: #4b4b4d;
    --stripe-blue: #6ccbee;
    --stripe-orange: #e0552a;
    --text-light: #ffffff;
    --text-muted: #bdbdbd;
  }
  * { box-sizing: border-box; margin: 0; padding: 0; }
  html, body {
    width: 1200px; height: 1078px; overflow: hidden;
    background: var(--backdrop);
    font-family: "Open Sans", Arial, sans-serif;
  }
  .card {
    position: absolute; left: 150px;
    width: 900px; height: 510px;
    background: var(--card);
    overflow: hidden;
    box-shadow: 0 10px 30px rgba(0,0,0,.45);
  }
  .card--back { top: 14px; }
  .card--front { top: 554px; }

  .band-vertical {
    position: absolute; top: 0; bottom: 0; left: 90px; width: 60px;
    background: var(--band);
  }
  .band-vertical .stripe { height: 40px; }

  .stripe--grey { background: var(--stripe-grey); }
  .stripe--blue { background: var(--stripe-blue); }
  .stripe--orange { background: var(--stripe-orange); }

  .logo-panel {
    position: absolute;
    background: radial-gradient(ellipse at center, var(--card-glow) 0%, var(--card) 70%);
    display: flex; align-items: center; justify-content: center; gap: 14px;
  }
  .card--back .logo-panel { left: 170px; top: 222px; width: 360px; height: 140px; }
  .card--front .logo-panel { left: 0; top: 0; width: 900px; height: 330px; }

  .logo-mark {
    flex: none; width: 30px; height: 30px; border-radius: 50%;
    background: var(--stripe-blue);
  }
  .logo-name {
    white-space: nowrap;
    color: var(--text-light); font-weight: 300; font-size: 40px; letter-spacing: 1px;
  }
  .card--front .logo-name { font-size: 58px; }
  .card--front .logo-mark { width: 42px; height: 42px; }

  .contact-block, .social-block {
    position: absolute; color: var(--text-light); font-size: 18px; line-height: 1.3;
    white-space: nowrap;
  }
  .contact-block { left: 190px; top: 30px; }
  .social-block { left: 570px; top: 150px; font-style: italic; }
  .block-heading {
    font-weight: 700; font-style: italic; font-size: 19px; letter-spacing: 1px;
    text-transform: uppercase; margin-bottom: 2px;
  }
  .contact-label {
    display: inline-block; width: 46px;
    color: var(--text-muted); font-size: 15px; text-transform: uppercase;
  }

  .person { position: absolute; right: 70px; top: 385px; text-align: left; }
  .person-name {
    color: var(--stripe-orange); font-weight: 700; font-size: 28px; text-transform: uppercase;
  }
  .person-title { color: var(--text-light); font-size: 18px; text-transform: uppercase; }

  .band-horizontal {
    position: absolute; left: 0; right: 0; top: 350px; height: 110px;
    background: var(--band); display: flex; align-items: stretch;
  }
  .band-horizontal .stripe { width: 50px; }
  .band-text {
    margin-left: auto; padding-right: 60px;
    display: flex; flex-direction: column; justify-content: center; align-items: flex-end;
  }
  .band-title {
    color: var(--stripe-orange); font-weight: 700; font-size: 44px; line-height: 1; text-transform: uppercase;
  }
  .band-name { color: var(--stripe-orange); font-weight: 700; font-size: 28px; }
</style>
</head>
<body>

<section class="card card--back" aria-label="Card back with contact details">
  <div class="band-vertical">
    <div class="stripe stripe--grey"></div>
    <div class="stripe stripe--blue"></div>
    <div class="stripe stripe--orange"></div>
  </div>

  <div class="contact-block">
    <p class="block-heading">Contact Us</p>
    <p><span class="contact-label">Work</span>012 555 0189</p>
    <p><span class="contact-label">Cell</span>012 555 0147</p>
    <p><span class="contact-label">Fax</span>012 555 0172</p>
    <p>evan@bytewardens.example</p>
    <p>www.bytewardens.example</p>
    <p>42 Relay Street, Suite 7, Westfield</p>
  </div>

  <div class="logo-panel">
    <span class="logo-mark"></span>
    <span class="logo-name">Byte Wardens</span>
  </div>

  <div class="social-block">
    <p class="block-heading">Follow us on social</p>
    <p>friendhub.example/user-name</p>
    <p>chirper.example/user-name</p>
    <p>folioset.example/user-name</p>
  </div>

  <div class="person">
    <p class="person-name">Evan Marlow</p>
    <p class="person-title">Founder</p>
  </div>
</section>

<section class="card card--front" aria-label="Card front with logo and title">
  <div class="logo-panel">
    <span class="logo-mark"></span>
    <span class="logo-name">Byte Wardens</span>
  </div>

  <div class="band-horizontal">
    <div class="stripe stripe--grey"></div>
    <div class="stripe stripe--blue"></div>
    <div class="stripe stripe--orange"></div>
    <div class="band-text">
      <p class="band-title">Founder</p>
      <p class="band-name">Evan Marlow</p>
    </div>
  </div>
</section>

</body>
</html>
```